New Business Card Design Project LORVANTI-Italy

we are LORVANTI-Italy
our company in the market for 3 years we are luxury cosmetic company and its about time for a facelift :)
i will like to have elegant luxurious and unique business card
that will give the person that get it a unique, luxurious and elegant impression
I'm VERY OPEN FOR NEW IDEAS , even duo i add a few files of things that i see on line and i like them

i add my logo as well
my website is LORVANTI.COM
(if you would like to see the main style that we have)

Target Market(s)

adult that have money :)

Industry/Entity Type

Business

Contact Information for Business Card

Name - Dario Lorvanti
Position - CEO and CO Founder
address - 4817 E Halvern
telephone - 555-384-1926
email - dario@lorvanti.com
fax - 555-384-1926
website - LORVANTI.COM

Colors
000000
959595
fbee3e
ffffff

Requirements
Must have
• big logo in GOLD color
• elegant look
• impressive
Nice to have
• not must but maybe classy pattern background
• not must but maybe emblem
• maybe clear plastic business card
Should not have
• colors
• images

```html
<!DOCTYPE html>
<html lang="en">
<head>
<meta charset="utf-8">
<title>LORVANTI-Italy Business Card</title>
<link href="https://fonts.googleapis.com/css2?family=Open+Sans:wght@400;600&display=swap" rel="stylesheet">
<style>
  :root {
    --backdrop: #2b2927;
    --card: #0d0d0d;
    --card-edge: #1a1a1a;
    --gold: #d6ab2e;
    --white: #ffffff;
    --grey: #959595;
  }
  * { margin: 0; padding: 0; box-sizing: border-box; }
  html, body { width: 1200px; height: 716px; overflow: hidden; }
  body {
    background: var(--backdrop);
    font-family: "Open Sans", sans-serif;
    position: relative;
  }
  .card {
    position: absolute;
    top: 210px;
    width: 520px;
    height: 297px;
    background: linear-gradient(150deg, #161616 0%, var(--card) 60%);
    border: 1px solid var(--card-edge);
    border-radius: 3px;
    box-shadow: 0 14px 30px rgba(0,0,0,0.45);
  }
  .card-front { left: 40px; }
  .card-back { left: 640px; }

  .brand {
    display: flex;
    align-items: center;
    gap: 12px;
    color: var(--gold);
    font-weight: 600;
    letter-spacing: 0.08em;
  }
  .brand-dot {
    border: 2px solid var(--gold);
    border-radius: 50%;
    flex: none;
  }
  .card-front .brand {
    position: absolute;
    left: 0; right: 0; top: 0; bottom: 0;
    flex-direction: column;
    justify-content: center;
    font-size: 30px;
  }
  .card-front .brand-dot { width: 70px; height: 70px; }

  .card-back .brand {
    position: absolute;
    left: 34px;
    top: 32px;
    flex-direction: column;
    align-items: center;
    gap: 8px;
    font-size: 15px;
  }
  .card-back .brand-dot { width: 36px; height: 36px; }

  .contact {
    position: absolute;
    right: 34px;
    bottom: 26px;
    width: 200px;
    color: var(--white);
  }
  .contact-name { font-size: 15px; font-weight: 600; line-height: 1.2; }
  .contact-role { font-size: 9px; color: var(--grey); line-height: 1.3; }
  .contact-rule { height: 1.5px; background: var(--gold); margin: 6px 0 8px; }
  .contact-list { list-style: none; }
  .contact-item {
    display: flex;
    align-items: center;
    gap: 8px;
    font-size: 12px;
    font-weight: 600;
    line-height: 1.65;
  }
  .contact-icon { width: 11px; height: 11px; fill: var(--gold); flex: none; }
</style>
</head>
<body>

<section class="card card-front">
  <div class="brand">
    <span class="brand-dot"></span>
    <span class="brand-name">LORVANTI ITALY</span>
  </div>
</section>

<section class="card card-back">
  <div class="brand">
    <span class="brand-dot"></span>
    <span class="brand-name">LORVANTI ITALY</span>
  </div>

  <div class="contact">
    <p class="contact-name">Dario Lorvanti</p>
    <p class="contact-role">Position - CEO and CO Founder</p>
    <div class="contact-rule"></div>
    <ul class="contact-list">
      <li class="contact-item">
        <svg class="contact-icon" viewBox="0 0 12 12"><path d="M2.5 0.8 L4.4 0.4 L5.3 3 L4 4 Q5 6.8 8 8 L9 6.7 L11.6 7.6 L11.2 9.5 Q10.6 11.4 8.6 11 Q2.3 9.4 1 3.4 Q0.7 1.4 2.5 0.8 Z"/></svg>
        555-384-1926
      </li>
      <li class="contact-item">
        <svg class="contact-icon" viewBox="0 0 12 12"><path d="M0.5 2.5 H11.5 V9.5 H0.5 Z M1.5 3.3 L6 6.6 L10.5 3.3" fill="none" stroke="#d6ab2e" stroke-width="1.1"/></svg>
        dario@lorvanti.com
      </li>
      <li class="contact-item">
        <svg class="contact-icon" viewBox="0 0 12 12"><path d="M3 0.5 H9 V3.5 H3 Z M0.5 4 H11.5 V9 H9.5 V11.5 H2.5 V9 H0.5 Z M3.5 8 V10.5 H8.5 V8 Z"/></svg>
        555-384-1926
      </li>
      <li class="contact-item">
        <svg class="contact-icon" viewBox="0 0 12 12"><circle cx="6" cy="6" r="5.2" fill="none" stroke="#d6ab2e" stroke-width="1.1"/><path d="M0.8 6 H11.2 M6 0.8 Q2.5 6 6 11.2 M6 0.8 Q9.5 6 6 11.2" fill="none" stroke="#d6ab2e" stroke-width="0.9"/></svg>
        LORVANTI.COM
      </li>
      <li class="contact-item">
        <svg class="contact-icon" viewBox="0 0 12 12"><path d="M6 0.4 Q10.2 0.4 10.2 4.6 Q10.2 7.4 6 11.6 Q1.8 7.4 1.8 4.6 Q1.8 0.4 6 0.4 Z M6 3 A1.6 1.6 0 1 0 6 6.2 A1.6 1.6 0 1 0 6 3 Z"/></svg>
        4817 E Halvern
      </li>
    </ul>
  </div>
</section>

</body>
</html>
```